Stage Design Company Business Card

We are looking to step up up our business card design for our team.

We are a Full service Design and Consultation company for Stage and TV with an emphasis in Theatrical Lighting.

We like our materials to be clean and modern with solid colors free of patterns and gradients. Our brand consists of 4 primary colors Purple, Black, Grey, and White. Provided is our Word Mark as well as our Symbol Logo.

We would like our cards to leave an impression beyond the information, show our attention to design and detail, and make our marks an easily recognized feature (together or apart) for our clients.

We need a warm approachable comfortable feel for some clients, and a professional flair for the board member type clients.

Attached are our brand elements, and our existing cards to give a sense of our style and a glipse at the information we provide on our cards.

Target Market(s)

broad client base from church leaders to high school teachers and architects.

Industry/Entity Type

Business

Contact Information for Business Card

We format our phone number with periods not parenthesis or dashes. Information will be edited for each of our team members, and team member specific cards are not part of this scope, but rather a template so to speak.

Font styles to use
Sans Serif

Colors
6b449b
ffffff
000000
333333
aaaaaa

Requirements
Must have
• Wordmark and logo mark present (does not need to exist on the same side of card)
• Brand Colors,
• Name, Phone, Email, Address.
• Unique choices that make someone stop and take a second look
Nice to have
• It would be nice to somehow convey what we DO, as our brand name does not lend itself to this, outside of an obvious tagline though.....
• social media if not crowded. all of our handles match (instagram, twitter, facebook)
Should not have
• "clipart"

```html
<!DOCTYPE html>
<html lang="en">
<head>
<meta charset="utf-8">
<title>Corvane Stage – Business Card</title>
<link href="https://fonts.googleapis.com/css2?family=Jost:wght@400;600&display=swap" rel="stylesheet">
<style>
  :root {
    --backdrop: #1c1c1c;
    --card: #262626;
    --ink: #ffffff;
    --ink-soft: #aaaaaa;
  }
  * { box-sizing: border-box; margin: 0; padding: 0; }
  html, body {
    width: 1200px; height: 900px; overflow: hidden;
    background: var(--backdrop);
    font-family: "Jost", sans-serif;
    color: var(--ink);
  }
  .stage { position: relative; width: 1200px; height: 900px; }
  .card {
    position: absolute; left: 290px; width: 620px; height: 354px;
    background: var(--card);
    box-shadow: 0 18px 40px rgba(0,0,0,.55);
  }
  .card--front { top: 60px; display: flex; flex-direction: column; align-items: center; justify-content: center; gap: 22px; }
  .card--back { top: 474px; display: flex; align-items: center; }

  .brand { display: flex; flex-direction: column; align-items: center; gap: 20px; }
  .brand__dot { width: 64px; height: 64px; border: 3px solid var(--ink); border-radius: 50%; }
  .brand__name { font-weight: 400; font-size: 26px; letter-spacing: 8px; text-transform: uppercase; color: var(--ink); }

  .back__brand { width: 300px; }
  .back__brand .brand__name { font-size: 22px; letter-spacing: 6px; }
  .divider { width: 2px; height: 190px; background: var(--ink); }

  .details { padding-left: 46px; }
  .details__name { font-weight: 600; font-size: 30px; letter-spacing: 1px; line-height: 1; }
  .details__role { font-size: 20px; margin-top: 2px; }
  .details__address { font-size: 18px; line-height: 1.2; margin-top: 18px; letter-spacing: .5px; }
  .contact { list-style: none; margin-top: 16px; font-size: 19px; letter-spacing: .5px; }
  .contact li { display: flex; align-items: center; gap: 14px; line-height: 1.35; }
  .contact svg { width: 16px; height: 16px; fill: none; stroke: var(--ink); stroke-width: 2; }
</style>
</head>
<body>
<main class="stage">
  <section class="card card--front" aria-label="Card front">
    <div class="brand">
      <span class="brand__dot"></span>
      <span class="brand__name">Corvane Stage</span>
    </div>
  </section>

  <section class="card card--back" aria-label="Card back">
    <div class="brand back__brand">
      <span class="brand__dot"></span>
      <span class="brand__name">Corvane Stage</span>
    </div>
    <span class="divider"></span>
    <div class="details">
      <h1 class="details__name">MILES R CORVANE</h1>
      <p class="details__role">Owner</p>
      <p class="details__address">52 E. Orchard ST<br>Tempe, AZ 85281</p>
      <ul class="contact">
        <li><svg viewBox="0 0 16 16"><rect x="4" y="1" width="8" height="14" rx="1.5"/><line x1="7" y1="12.5" x2="9" y2="12.5"/></svg>800.555.0142</li>
        <li><svg viewBox="0 0 16 16"><rect x="1.5" y="3.5" width="13" height="9"/><polyline points="1.5,3.5 8,9 14.5,3.5"/></svg>info@corvane-s.com</li>
        <li><svg viewBox="0 0 16 16"><circle cx="7" cy="7" r="4.5"/><line x1="10.3" y1="10.3" x2="14.5" y2="14.5"/></svg>corvane-s.com</li>
      </ul>
    </div>
  </section>
</main>
</body>
</html>
```